Cruise Booking Website

Cruise search and booking website

This project is a redesign of a cruise booking website we did a few years ago.

The current website is located here: http://voyage.pylonworks.example/en/

It's not fully functional but gives you ad idea how miserable the old design was.

All the information about cruises, cruise lines, destinations, ports and shore excursions will be similar to http://www.sailquest.example/
Actual search pages (form, results, single result, sailing and cabin selection, ship info, booking) will have EXACTLY the same info as sailquest.example

We like the style of http://harborfleetdesk.example, it's quite modern, good spacing, not overloaded with information. So you can use it as an example of what we like, not what we want as a final result for us. Please, don't copy it. The result should not be possible to resemble the harborfleetdesk.example, because our site has to be unique. This is important!
If you submit a design that clearly reminds another cruise site it will be rejected!

Also the mockup provided is just to give you the basic structure and show what information has to be present on the page. It doesn't mean the layout has to be the same as a mockup. The layout is up to the designer.

I've updated the mockup to be more generic so it doesn't confuse you:
https://files.boxvault.example/s/k7m2qp9wz4hx/Home%20page.png

When you're adding social sharing icons like plazanet/chirpline you have to use chinese ones instead:
https://files.boxvault.example/s/t3nr8vx5lc2e/chinese-social-icons.png
Originals: http://minilk.example/qR7t

We'll start with home page first and after it's approved inner pages can be designed.

I know the cost of the project doesn't look high, but the task is straight forward and doesn't require to be very original, it's better to follow existing design and layout patterns that proved to work well.
That's why I encourage you to choose a template to build the design on top of one of https://themeparlor.example/ themes if it will save the design work, will be easier and faster for you. So it will be more like a customization than a new design from scratch.

Mockups, site map and logo files:
- https://files.boxvault.example/sh/h48dm2rs73fkpw/QvnbW2Xz8e

Website tree:
- https://sheets.papernest.example/document/d/7xPqR2mLw9sTk4VbN8cHj3YzA6eUf5GdKo1iMnBv/edit?usp=sharing
Updates

So far a lot of designs are just copying http://www.harborfleetdesk.example/ - we don't like it!

We like the style of harborfleetdesk.example, it's quite modern, good spacing, not overloaded with information. So you can use it as an example of what we like, not what we want as a final result for us. Please, don't copy it. The result should not be possible to resemble the harborfleetdesk.example, because our site has to be unique. This is important!

Target Market(s)

Chinese travellers

Industry/Entity Type

Build

Requirements
Must have
• * White, blue and red
* Large spacing, not too much information cramped into a small space like sailquest.example or the current website
* More "hidden" info in popups, tabs and so on, so not to many things are visible at the same time
* Compatible with kestrel scaffold styling (for easier coding):
- http://kestrelkit.codeshelf.example/scaffold/index.html
- http://skinmarket.example/
* Feel free to propose to build the design on top of one of https://themeparlor.example/ themes if it will save the design work, will be easier and faster for you

```html
<!DOCTYPE html>
<html lang="en">
<head>
<meta charset="utf-8">
<title>SeaVista Cruises – Home</title>
<link href="https://fonts.googleapis.com/css2?family=Titillium+Web:wght@300;400;600;700&family=Arimo:wght@400;700&display=swap" rel="stylesheet">
<style>
:root{
  --red:#e2443a;
  --blue:#4fb0ef;
  --navy:#1f4f74;
  --teal:#15636f;
  --cyan:#3fd6e6;
  --grey:#e8e8e8;
  --light:#f3f3f3;
  --text:#333;
  --white:#fff;
}
*{box-sizing:border-box;margin:0;padding:0}
html,body{width:787px;height:1200px;overflow:hidden;background:var(--white)}
body{position:relative;font-family:"Arimo",Arial,sans-serif;color:var(--text);font-size:9px}
.abs{position:absolute;white-space:nowrap}
.head{position:absolute;left:0;top:0;width:787px;height:337px;background:linear-gradient(180deg,#2d6e9c 0%,#3a7aa6 30%,#2f6a95 70%,#2a5f87 100%);border-bottom:2px solid var(--red)}
.hero-photo{position:absolute;left:0;top:88px;width:787px;height:249px;background:linear-gradient(160deg,#4a88b4 0%,#2f6c99 45%,#1f5882 100%)}
.brand{left:32px;top:12px;display:flex;align-items:center;gap:6px;color:var(--white);font-family:"Titillium Web",sans-serif}
.brand .dot{width:28px;height:28px;border-radius:50%;background:var(--white)}
.brand b{font-size:24px;font-weight:700;line-height:1}
.brand small{display:block;font-size:9px;font-weight:400}
.search{left:496px;top:14px}
.search .field{width:114px;height:15px;border-radius:8px;background:var(--white);border:2px solid #cfd8de}
.search .go{position:absolute;left:120px;top:-1px;color:var(--white);font-family:"Titillium Web",sans-serif;font-size:12px}
.search a{display:block;color:var(--white);font-size:8px;margin-top:4px;text-decoration:underline}
.quick{left:678px;top:5px;width:80px}
.quick a{display:block;color:var(--white);font-size:9px;line-height:11px;border-bottom:1px solid var(--white);padding:2px 0 1px;text-decoration:none;letter-spacing:.2px;font-family:"Titillium Web",sans-serif;white-space:nowrap}
.quick a:last-child{border-bottom:0}
.nav{left:29px;top:59px;width:729px;height:28px;background:var(--grey);display:flex;align-items:center;padding-left:22px}
.nav a{font-family:"Arimo",sans-serif;font-size:9.5px;color:#333;text-decoration:none;padding:0 11px 0 4px;margin-right:4px;height:28px;line-height:28px;position:relative;white-space:nowrap}
.nav a::after{content:"";position:absolute;right:2px;top:11px;width:4px;height:4px;border-right:1.2px solid var(--red);border-bottom:1.2px solid var(--red);transform:rotate(45deg)}
.nav a.on{background:var(--red);color:var(--white)}
.nav a.on::after{border-color:var(--white)}
.hero-title{left:96px;top:106px;color:var(--cyan);font-family:"Titillium Web",sans-serif;font-weight:300;font-size:23px;line-height:24px;letter-spacing:1px}
.prize{left:100px;top:168px;width:130px;height:132px;background:var(--teal);border:2px solid var(--cyan);outline:5px solid rgba(255,255,255,.25);text-align:center;color:var(--cyan);font-family:"Titillium Web",sans-serif;padding-top:10px}
.prize .l1{font-size:17px;font-weight:600;line-height:18px}
.prize .l1 b{color:var(--white);font-weight:600}
.prize .amt{font-size:28px;font-weight:300;line-height:32px}
.prize .big{color:var(--white);font-size:25px;font-weight:700;line-height:24px}
.prize .sub{font-size:9px;letter-spacing:.5px}
.dest-tile{width:62px;height:62px;background:rgba(255,255,255,.55);padding:4px}
.dest-tile div{width:100%;height:100%;background:var(--teal);border:1px solid var(--cyan);color:var(--cyan);font-size:7.5px;text-align:center;padding-top:4px;line-height:8px;font-family:"Arimo",sans-serif}
.dest-tile i{display:block;width:22px;height:22px;margin:6px auto 0;border-radius:50%;background:rgba(255,255,255,.25)}
.badge{left:398px;top:242px;width:62px;height:62px;border-radius:50%;background:var(--white);border:3px solid #ddd}
.find-more{left:410px;top:269px;width:154px;height:32px;background:linear-gradient(180deg,#5fe3ee,#2ec2d6);color:var(--navy);font-family:"Titillium Web",sans-serif;font-weight:700;font-size:15px;line-height:32px;padding-left:56px;letter-spacing:1px}
.arrow-btn{width:24px;height:54px;background:rgba(20,60,90,.6)}
.panel{left:588px;top:108px;width:141px;height:196px;background:var(--white);border-radius:2px}
.panel h3{height:18px;background:var(--red);color:var(--white);font-family:"Titillium Web",sans-serif;font-size:11.5px;letter-spacing:.5px;text-align:center;line-height:18px;font-weight:600}
.sel{position:absolute;height:12px;border:1px solid #999;font-size:7.5px;line-height:10px;padding-left:2px;color:var(--navy)}
.sel::after{content:"";position:absolute;right:0;top:0;width:9px;height:10px;border-left:1px solid #999}
.plab{position:absolute;font-size:7px;color:var(--navy);font-weight:700;white-space:nowrap}
.panel .go{position:absolute;left:6px;top:174px;width:128px;height:13px;background:#2f6f96;color:var(--white);text-align:center;font-size:9px;line-height:13px;font-family:"Titillium Web",sans-serif;letter-spacing:.5px;font-weight:600}
.bar{left:0;top:339px;width:787px;height:57px;background:var(--light)}
.hotline{left:29px;top:346px;width:169px;height:38px;border:1px solid var(--blue);background:var(--white);display:flex;align-items:center;padding-left:10px;gap:6px;font-size:9.5px;color:var(--navy)}
.hotline b{font-family:"Titillium Web",sans-serif;font-weight:400;font-size:14px}
.util{top:358px;font-size:9.5px;color:#222;display:flex;align-items:center;gap:5px}
.newsletter{left:591px;top:351px;width:167px;height:31px;background:var(--blue);color:var(--white);font-family:"Titillium Web",sans-serif;font-size:13.5px;text-align:center;line-height:31px}
h1.section{left:29px;top:400px;font-family:"Titillium Web",sans-serif;font-weight:400;font-size:21px;color:#222}
.intro{left:29px;top:434px;width:730px;font-size:8.5px;line-height:12px;color:#444;font-family:"Titillium Web",sans-serif;white-space:normal}
.tabs{left:29px;top:478px;width:729px;height:22px;border-bottom:1px solid var(--red);display:flex}
.tabs span{width:127px;height:22px;border:1px solid var(--red);text-align:center;line-height:20px;font-size:10px;font-weight:700;font-family:"Titillium Web",sans-serif;color:#333}
.tabs span.on{background:var(--red);color:var(--white)}
.card{width:169px;height:138px;background:var(--grey)}
.card .ph{height:92px}
.card h4{font-family:"Arimo",sans-serif;font-weight:400;font-size:10px;margin:10px 0 0 8px;color:#222}
.more{display:flex;align-items:center;margin:3px 0 0 8px;width:68px;height:11px;background:var(--white);font-size:7.5px;color:var(--red);font-weight:700}
.more i{width:11px;height:11px;background:var(--red);color:var(--white);font-style:normal;text-align:center;line-height:11px;margin-right:8px;font-size:10px}
.deals{left:29px;top:834px;width:729px;height:138px;background:linear-gradient(180deg,#e0e0e0,#ececec);border:2px solid #ddd}
.deals h2{position:absolute;left:3px;top:2px;width:719px;height:24px;background:var(--white);font-family:"Titillium Web",sans-serif;font-weight:400;font-size:17px;padding-left:10px;line-height:24px;color:#333}
.deal{position:absolute;top:34px;width:122px}
.deal .ph{height:66px;border:2px solid var(--blue)}
.deal p{background:var(--light);padding:6px 6px 4px;font-size:7.5px;line-height:10px;color:#222}
.deal p span{color:var(--red)}
.tri{position:absolute;top:66px;width:0;height:0;border-top:4px solid transparent;border-bottom:4px solid transparent}
.partners{left:0;top:1010px;width:787px;height:53px;background:var(--red);color:var(--white)}
.partners h2{position:absolute;left:34px;top:11px;font-family:"Titillium Web",sans-serif;font-weight:300;font-size:21px}
.plogo{position:absolute;top:19px;font-family:"Titillium Web",sans-serif;font-size:9.5px;font-weight:600;white-space:nowrap}
.foot{left:0;top:1063px;width:787px;height:137px;background:var(--blue)}
.links{position:absolute;top:22px;list-style:none;font-size:7.5px;color:#12233a;line-height:13.5px;white-space:nowrap}
.links li::before{content:"";display:inline-block;width:3px;height:3px;background:var(--white);margin-right:6px;vertical-align:middle}
.soc{position:absolute;width:19px;height:19px;border-radius:3px;background:var(--white);opacity:.85}
.foot hr{position:absolute;left:29px;top:98px;width:729px;border:0;border-top:1px solid #2d6e9c}
.copy{position:absolute;left:0;top:104px;width:787px;text-align:center;font-size:7.5px;line-height:13px;color:#111}
</style>
</head>
<body>

<header class="head">
  <div class="hero-photo" role="img" aria-label="Cruise ship deck over open blue sea"></div>
  <div class="abs brand"><span class="dot"></span><div><b>SeaVista</b><small>www.seavista.example</small></div></div>
  <div class="abs search"><div class="field"></div><span class="go">Search</span><a>Advance Search</a></div>
  <nav class="abs quick"><a>BOOKING</a><a>ONLINE BOOKING</a><a>MEMBERS CENTRE</a></nav>
  <nav class="abs nav">
    <a class="on">DESTINATIONS</a><a>CRUISE LINES</a><a>SHORE ACTIVITIES</a><a>PROMOTIONS</a><a>CRUISE NEWS</a><a>BLOG</a><a>FAQ(Q&amp;A)</a><a>CONTACT US</a>
  </nav>

  <div class="abs arrow-btn" style="left:29px;top:194px"><svg width="24" height="54"><path d="M15 20l-6 7 6 7" stroke="#fff" stroke-width="2" fill="none"/></svg></div>
  <div class="abs arrow-btn" style="left:735px;top:194px"><svg width="24" height="54"><path d="M9 20l6 7-6 7" stroke="#fff" stroke-width="2" fill="none"/></svg></div>

  <div class="abs hero-title">CRAZY CRUISE VACATIONS<br>&amp; GRAB MUCH MORE</div>
  <div class="abs prize">
    <div class="l1">HURRY<br><span style="font-size:13px">TO </span><b>WIN A</b></div>
    <div class="amt">$6000</div>
    <div class="big">CRUISE</div>
    <div class="sub">VACATION FOR 2</div>
  </div>
  <div class="abs dest-tile" style="left:246px;top:164px"><div>MEXICO<i role="img" aria-label="Sombrero icon"></i></div></div>
  <div class="abs dest-tile" style="left:321px;top:164px"><div>JAPAN<i role="img" aria-label="Pagoda icon"></i></div></div>
  <div class="abs dest-tile" style="left:246px;top:240px"><div>WESTERN<br>CARIBBEAN<i role="img" aria-label="Palm tree icon" style="margin-top:2px"></i></div></div>
  <div class="abs dest-tile" style="left:321px;top:240px"><div>EUROPE<i role="img" aria-label="Eiffel tower icon"></i></div></div>
  <div class="abs find-more">FIND MORE ›</div>
  <div class="abs badge"></div>

  <form class="abs panel">
    <h3>FIND YOUR CRUISE</h3>
    <div class="sel" style="left:5px;top:26px;width:130px">Popular Destinations</div>
    <div class="sel" style="left:5px;top:51px;width:62px">Any Length</div>
    <div class="sel" style="left:73px;top:51px;width:62px">Any Month</div>
    <div class="sel" style="left:5px;top:77px;width:130px">Any Cruise Lines</div>
    <div class="plab" style="left:6px;top:101px;font-size:8px;font-weight:400;border-bottom:1px solid #999;width:128px;padding-bottom:2px">NUMBER OF TRAVELERS</div>
    <div class="plab" style="left:6px;top:121px">AGE 25+</div>
    <div class="plab" style="left:73px;top:121px">AGE 0-24</div>
    <div class="sel" style="left:5px;top:131px;width:62px">2</div>
    <div class="sel" style="left:73px;top:131px;width:62px">0</div>
    <div class="sel" style="left:6px;top:154px;width:11px;height:11px;border-color:#bbb"></div>
    <div class="plab" style="left:22px;top:156px;font-weight:400">Check for Rates</div>
    <div class="go">SEARCH CRUISE</div>
  </form>
</header>

<section class="abs bar"></section>
<div class="abs hotline">
  <svg width="18" height="26" viewBox="0 0 18 26"><path d="M4 2c-3 2-3 6 0 13s6 10 9 9l3-2-4-5-3 1c-2-2-3-5-3-7l2-2-2-7z" fill="#e2443a"/></svg>
  <span>Hotline:</span><b>4000 123 456</b>
</div>
<div class="abs util" style="left:404px">
  <svg width="16" height="16"><rect x="1" y="3" width="11" height="11" fill="none" stroke="#e2443a" stroke-width="1.5"/><path d="M6 10l8-8" stroke="#e2443a" stroke-width="2"/></svg>REGISTER
</div>
<div class="abs util" style="left:490px">
  <svg width="16" height="16"><rect x="4" y="1" width="10" height="13" fill="none" stroke="#e2443a" stroke-width="1.5"/><path d="M1 8h7M6 5l3 3-3 3" stroke="#e2443a" stroke-width="1.5" fill="none"/></svg>MY ACCOUNT
</div>
<div class="abs newsletter">Cruise Deals Newsletters</div>

<h1 class="abs section">Destinations</h1>
<p class="abs intro">Cruising offers a broad range of destinations to choose from. Whether you are a first time cruiser looking to stay close to home or an experienced world explorer looking for a new and interesting place to seek adventure the cruise opportunities span the globe.</p>

<div class="abs tabs"><span class="on">Featured Destinations</span><span style="border-left:0">All Destinations</span></div>

<article class="abs card" style="left:29px;top:524px"><div class="ph" role="img" aria-label="Travellers relaxing on a wooden boat by turquoise water" style="background:linear-gradient(135deg,#6b5a44,#8fc9cf)"></div><h4>Africa</h4><div class="more"><i>+</i>Read More</div></article>
<article class="abs card" style="left:216px;top:524px"><div class="ph" role="img" aria-label="Cruise ship beside glacier and snowy mountains" style="background:linear-gradient(180deg,#b7c8da,#5f87a8 60%,#2f5f84)"></div><h4>Alaska</h4><div class="more"><i>+</i>Read More</div></article>
<article class="abs card" style="left:404px;top:524px"><div class="ph" role="img" aria-label="Limestone cliffs over a tropical lagoon" style="background:linear-gradient(135deg,#3c7a4a,#2bb6c4 70%,#dfe9d8)"></div><h4>Asia-Pacific &amp; Middle East</h4><div class="more"><i>+</i>Read More</div></article>
<article class="abs card" style="left:590px;top:524px"><div class="ph" role="img" aria-label="White cruise ship at sea under blue sky" style="background:linear-gradient(180deg,#6ea9e0,#d9e6f1 55%,#1b5c9c)"></div><h4>Caribbean</h4><div class="more"><i>+</i>Read More</div></article>

<article class="abs card" style="left:29px;top:679px"><div class="ph" role="img" aria-label="Cruise ship in harbour near city opera house" style="background:linear-gradient(180deg,#2a5f8a,#b68e55 45%,#1f5a7d)"></div><h4>Australia &amp; New Zealand</h4><div class="more"><i>+</i>Read More</div></article>
<article class="abs card" style="left:216px;top:679px"><div class="ph" role="img" aria-label="Swimmers in clear shallow water at a beach" style="background:linear-gradient(180deg,#8ec7e6,#7fd3d6 50%,#e6dcc2)"></div><h4>Bahamas</h4><div class="more"><i>+</i>Read More</div></article>
<article class="abs card" style="left:404px;top:679px"><div class="ph" role="img" aria-label="Pink sand beach with green hills" style="background:linear-gradient(160deg,#3e7a3a,#e0c6b4 50%,#2ea2b5)"></div><h4>Bermuda</h4><div class="more"><i>+</i>Read More</div></article>
<article class="abs card" style="left:590px;top:679px"><div class="ph" role="img" aria-label="Coastline with turquoise sea and hotels" style="background:linear-gradient(100deg,#3fc2c0,#a9dfd7 55%,#b7b5a7)"></div><h4>Central &amp; South America</h4><div class="more"><i>+</i>Read More</div></article>

<section class="abs deals">
  <h2>Last Minute Deals</h2>
  <span class="tri" style="left:10px;border-right:7px solid #777"></span>
  <span class="tri" style="left:712px;border-left:7px solid #777"></span>
  <div class="deal" style="left:58px"><div class="ph" role="img" aria-label="Couple relaxing on a sailing boat" style="background:linear-gradient(135deg,#6f9cb8,#2c6a92)"></div><p>3 Days Bahamas<br>for <span>$ 9000</span></p></div>
  <div class="deal" style="left:224px"><div class="ph" role="img" aria-label="Couple swimming in the sea" style="background:linear-gradient(180deg,#5aa9c8,#2b7fa3)"></div><p>Australia &amp; New Zealand<br>for <span>$ 9000</span></p></div>
  <div class="deal" style="left:388px"><div class="ph" role="img" aria-label="Couple on a ship deck over the ocean" style="background:linear-gradient(180deg,#9cc7e6,#3a7fb7)"></div><p>Bermuda<br>for <span>$ 9000</span></p></div>
  <div class="deal" style="left:554px"><div class="ph" role="img" aria-label="People riding a banana boat" style="background:linear-gradient(180deg,#3c78a8,#234f7c)"></div><p>Bermuda<br>for <span>$ 9000</span></p></div>
</section>

<section class="abs partners">
  <h2>Our Reliable Partners</h2>
  <svg class="abs" style="left:258px;top:20px" width="10" height="12"><path d="M7 1L2 6l5 5" stroke="#fff" stroke-width="2" fill="none"/></svg>
  <span class="plogo" style="left:280px">NORTHWIND LINES</span>
  <span class="plogo" style="left:382px">Corallo</span>
  <span class="plogo" style="left:455px">REGENT TIDE</span>
  <span class="plogo" style="left:562px">Harbor Star Line</span>
  <span class="plogo" style="left:670px">MARIS CRUISES</span>
  <svg class="abs" style="left:754px;top:20px" width="10" height="12"><path d="M3 1l5 5-5 5" stroke="#fff" stroke-width="2" fill="none"/></svg>
</section>

<footer class="abs foot">
  <ul class="links" style="left:96px"><li>Visa</li><li>About us</li><li>Contact us</li><li>Payment info</li></ul>
  <ul class="links" style="left:257px"><li>Terms of privacy</li><li>Terms of service</li><li>Terms of insurance</li><li>Cooperation network</li></ul>
  <ul class="links" style="left:440px"><li>Registration agreement</li><li>Cruise promotion policy</li><li>Booking process explanation</li><li>Bonus points collection policy</li></ul>
  <span class="soc" style="left:633px;top:18px"></span><span class="soc" style="left:670px;top:18px"></span>
  <span class="soc" style="left:633px;top:40px"></span><span class="soc" style="left:670px;top:40px"></span>
  <span class="soc" style="left:633px;top:62px"></span><span class="soc" style="left:670px;top:62px"></span>
  <hr>
  <p class="copy">Copyright © 2011 SeaVista Cruise Network<br>ICP License 10000000</p>
</footer>

</body>
</html>
```